Modern Verdell Tree Care Website

I need a website for a full service Tree Care company. The company provides tree pruning, tree removal, tree preservation, emergency services, stump grinding, and emergency tree services.

Target Market(s)

Customers that need tree services

Industry/Entity Type

Landscaping, Tree Services

Coding

Coded - Design and coding required

Number of Pages Required

5+ page

Font styles to use
Sans Serif

Requirements
Must have
• Good clean design that showcases the services the company provides.
Nice to have
• Services page; contact form, blog, home page, about page

```html
<!DOCTYPE html>
<html lang="en">
<head>
<meta charset="utf-8">
<title>Verdell Tree Care</title>
<link href="https://fonts.googleapis.com/css2?family=Oswald:wght@500;600;700&family=Open+Sans:wght@400;600;700&display=swap" rel="stylesheet">
<style>
:root{
  --green:#8cc63f;
  --orange:#f9a82b;
  --ink:#111111;
  --text:#555555;
  --soft:#f5f8ee;
  --dark:#1b0e0e;
  --white:#ffffff;
}
*{margin:0;padding:0;box-sizing:border-box}
html,body{width:1200px;height:5240px;overflow:hidden}
body{position:relative;background:var(--white);font-family:'Open Sans',sans-serif;color:var(--text)}
.abs{position:absolute}
.heading{font-family:'Oswald',sans-serif;font-weight:700;text-transform:uppercase;color:var(--ink);letter-spacing:.5px}
.btn{position:absolute;background:var(--orange);color:var(--ink);font-family:'Open Sans',sans-serif;font-weight:700;border-radius:6px;display:flex;align-items:center;justify-content:center;box-shadow:0 3px 8px rgba(0,0,0,.12)}
.btn-sm{font-size:12px;height:34px;width:110px}
.photo{position:absolute}

/* header */
.site-header{position:absolute;left:0;top:0;width:1200px;height:150px;background:var(--white)}
.site-header::before{content:"";position:absolute;left:0;top:0;width:100%;height:4px;background:var(--green)}
.brand{position:absolute;left:110px;top:34px;display:flex;align-items:center;gap:14px}
.brand-mark{width:58px;height:58px;background:var(--green)}
.brand-name{font-family:'Oswald',sans-serif;font-weight:600;font-size:34px;line-height:36px;color:var(--green);text-transform:uppercase;letter-spacing:2px}
.main-nav{position:absolute;top:96px;left:510px;display:flex;gap:0}
.main-nav a{font-family:'Open Sans',sans-serif;font-weight:700;font-size:15px;color:var(--ink);text-decoration:none;margin-right:56px}
.main-nav a:last-child{margin-right:0}

/* hero */
.hero{position:absolute;left:0;top:150px;width:1200px;height:620px;overflow:hidden}
.hero-photo{left:0;top:0;width:100%;height:100%;background:linear-gradient(100deg,#3c3a2c 0%,#6b5a3e 30%,#8a8475 48%,#4e4b48 65%,#7d7766 85%,#a9a18a 100%)}
.hero-shade{position:absolute;left:0;top:0;width:60%;height:100%;background:linear-gradient(90deg,rgba(20,18,12,.65),rgba(20,18,12,0))}
.hero-title{position:absolute;left:110px;top:100px;font-family:'Oswald',sans-serif;font-weight:700;text-transform:uppercase;line-height:118px}
.hero-title .l1{display:block;color:var(--green);font-size:104px}
.hero-title .l2{display:block;color:var(--white);font-size:104px}
.hero-lead{position:absolute;left:110px;top:346px;width:440px;color:var(--white);font-size:16px;line-height:32px}
.hero .btn{left:110px;top:432px;width:138px;height:40px;font-size:15px}

/* intro & about */
.section-title{position:absolute;left:0;width:1200px;text-align:center;font-family:'Oswald',sans-serif;font-weight:700;font-size:46px;color:var(--green);text-transform:uppercase}
.section-title .accent{color:var(--orange)}
.section-lead{position:absolute;left:0;width:1200px;text-align:center;font-size:14px;line-height:32px;color:var(--text)}
.about-photo{left:112px;top:1066px;width:488px;height:462px;background:linear-gradient(160deg,#5f5a49,#7b7a57 40%,#5b7d3a 70%,#7a9a4c)}
.arrow-box{position:absolute;left:536px;top:1464px;width:64px;height:64px;background:var(--orange);display:flex;align-items:center;justify-content:center}
.about-title{position:absolute;left:665px;top:1080px;font-size:44px}
.body-copy{font-size:13px;line-height:29px;color:var(--text)}
.about-copy{position:absolute;left:665px;top:1150px;width:400px}
.about-copy p+p{margin-top:29px}

/* services */
.services{position:absolute;left:0;top:1664px;width:1200px;height:1641px;background:var(--soft)}
.svc-bar{position:absolute;width:7px;height:294px;background:var(--ink);border-radius:3px}
.svc-title{position:absolute;font-size:38px}
.svc-copy{position:absolute;width:430px}
.svc-copy p+p{margin-top:29px}
.svc-accent{position:absolute;background:var(--green)}
.svc-photo{box-shadow:0 12px 30px rgba(0,0,0,.12)}
.right{text-align:right}

/* news */
.news-card{position:absolute;top:3590px;width:316px}
.news-photo{position:relative;width:316px;height:256px}
.news-date{position:absolute;left:20px;top:240px;width:92px;height:28px;background:var(--orange);color:var(--ink);font-size:12px;font-weight:600;display:flex;align-items:center;justify-content:center}
.news-title{margin:34px 26px 0;font-size:13px;font-weight:700;line-height:28px;color:var(--ink)}
.news-text{margin:12px 26px 0;font-size:10px;line-height:22px;color:var(--text)}

/* contact */
.contact{position:absolute;left:112px;top:4139px;width:976px;height:503px;background:var(--orange);border-radius:60px}
.contact-photo{left:30px;top:43px;width:413px;height:419px;border-radius:40px;background:linear-gradient(150deg,#3f6a28,#6e8f44 45%,#4c7030 70%,#8aa963)}
.contact-title{position:absolute;left:492px;top:72px;font-family:'Oswald',sans-serif;font-weight:600;font-size:42px;color:var(--white);letter-spacing:1.5px}
.contact-sub{position:absolute;left:492px;top:126px;font-size:13px;color:var(--white)}
.field{position:absolute;background:var(--white);border-radius:8px;font-size:11px;color:#666;padding:12px 16px}
.send{position:absolute;left:492px;top:4568px;left:492px;top:429px;font-size:11px;font-weight:700;color:var(--white);text-decoration:underline;letter-spacing:.5px}

/* footer */
.site-footer{position:absolute;left:0;top:4790px;width:1200px;height:450px;background:var(--dark)}
.footer-brand{position:absolute;left:0;top:172px;width:1200px;display:flex;justify-content:center;align-items:center;gap:18px}
.footer-brand .brand-mark{width:74px;height:74px;background:var(--white)}
.footer-brand .brand-name{color:var(--white);font-size:42px;line-height:44px}
.footer-nav{position:absolute;left:0;top:300px;width:1200px;display:flex;justify-content:center;align-items:center;font-size:13px;color:var(--white)}
.footer-nav span.sep{margin:0 56px;opacity:.9}
.socials{position:absolute;top:350px;left:502px;display:flex;gap:13px}
.socials span{width:28px;height:28px;background:var(--green);display:block}
.copyright{position:absolute;top:400px;left:0;width:1200px;text-align:center;font-size:11px;color:var(--white)}
</style>
</head>
<body>

<header class="site-header">
  <div class="brand"><span class="brand-mark"></span><span class="brand-name">Verdell<br>Tree Care</span></div>
  <a class="btn" style="left:950px;top:36px;width:136px;height:40px;font-size:15px;font-weight:600">Get Started</a>
  <nav class="main-nav">
    <a>HOME</a><a>ABOUT US</a><a>OUR SERVICES</a><a>BLOGS</a><a>CONTACT</a>
  </nav>
</header>

<section class="hero">
  <div class="photo hero-photo" role="img" aria-label="Arborist in helmet and harness cutting a tree trunk with a chainsaw"></div>
  <div class="hero-shade"></div>
  <h1 class="hero-title"><span class="l1">Verdell</span><span class="l2">Tree Care</span></h1>
  <p class="hero-lead">Perspiciatis unde omnis iste natus error sit voluptatem accusantium doloremque laudantium</p>
  <a class="btn">Get Started</a>
</section>

<h2 class="section-title" style="top:890px">Full Service <span class="accent">Tree Care</span> Company</h2>
<p class="section-lead" style="top:966px">Lorem ipsum dolor sit amet, consectetur adipiscing elit, sed do eiusmod tempor incididunt ut labore et dolore magna aliqua.<br>Quis ipsum suspendisse ultrices gravida. Risus commodo viverra maecenas accumsan lacus vel facilisis.</p>

<div class="photo about-photo" role="img" aria-label="Worker in high-visibility vest pruning branches from a ladder"></div>
<div class="arrow-box"><svg width="26" height="16" viewBox="0 0 26 16"><path d="M1 8h22M16 2l7 6-7 6" stroke="#111" stroke-width="2.6" fill="none"/></svg></div>
<h2 class="heading about-title">About Us</h2>
<div class="about-copy body-copy">
  <p>I must explain to you how all this mistaken idea of denouncing pleasure and praising pain was born and I will give you a complete account of the system, and expound the actual teachings of the great explorer of the truth, the master-builder of human happiness. No one rejects, dislikes, or avoids pleasure itself, because it is pleasure, but because those who do not know how to pursue pleasure rationally encounter consequences that are extremely painful.</p>
  <p>Nor again is there anyone who loves or pursues or desires to obtain pain of itself, because it is pain</p>
</div>
<a class="btn btn-sm" style="left:665px;top:1472px">Read More</a>

<section class="services">
  <!-- pruning -->
  <div class="svc-bar" style="left:112px;top:134px"></div>
  <h3 class="heading svc-title" style="left:169px;top:122px">Tree Pruning</h3>
  <div class="svc-copy body-copy" style="left:169px;top:190px">
    <p>I must explain to you how all this mistaken idea of denouncing pleasure and praising pain was born and I will give you a complete account of the system, and expound the actual teachings of the great explorer of the truth, the master-builder of human happiness.</p>
    <p>No one rejects, dislikes, or avoids pleasure itself, because it is pleasure, but because those</p>
  </div>
  <a class="btn btn-sm" style="left:169px;top:415px">Read More</a>
  <div class="svc-accent" style="left:675px;top:252px;width:193px;height:209px"></div>
  <div class="photo svc-photo" style="left:706px;top:126px;width:382px;height:305px;background:linear-gradient(170deg,#2f4a2a,#53703d 45%,#8e8a70 70%,#3d5a30)" role="img" aria-label="Arborist on an aerial lift beside a tall trimmed trunk among pines"></div>

  <!-- removal -->
  <div class="svc-accent" style="left:334px;top:744px;width:191px;height:210px"></div>
  <div class="photo svc-photo" style="left:112px;top:618px;width:382px;height:305px;background:linear-gradient(140deg,#5b4428,#a06a2c 40%,#c9862e 65%,#6e4a22)" role="img" aria-label="Chainsaw cutting a fallen log among autumn leaves"></div>
  <h3 class="heading svc-title right" style="right:169px;top:614px">Tree Removal</h3>
  <div class="svc-copy body-copy right" style="right:169px;top:682px">
    <p>I must explain to you how all this mistaken idea of denouncing pleasure and praising pain was born and I will give you a complete account of the system, and expound the actual teachings of the great explorer of the truth, the master-builder of human happiness.</p>
    <p>No one rejects, dislikes, or avoids pleasure itself, because it is pleasure, but because those</p>
  </div>
  <a class="btn btn-sm" style="left:921px;top:909px">Read More</a>
  <div class="svc-bar" style="left:1081px;top:624px"></div>

  <!-- preservation -->
  <div class="svc-bar" style="left:112px;top:1116px"></div>
  <h3 class="heading svc-title" style="left:169px;top:1104px">Tree Preservation</h3>
  <div class="svc-copy body-copy" style="left:169px;top:1172px">
    <p>I must explain to you how all this mistaken idea of denouncing pleasure and praising pain was born and I will give you a complete account of the system, and expound the actual teachings of the great explorer of the truth, the master-builder of human happiness.</p>
    <p>No one rejects, dislikes, or avoids pleasure itself, because it is pleasure, but because those</p>
  </div>
  <a class="btn btn-sm" style="left:169px;top:1397px">Read More</a>
  <div class="svc-accent" style="left:675px;top:1234px;width:193px;height:209px"></div>
  <div class="photo svc-photo" style="left:706px;top:1108px;width:382px;height:305px;background:linear-gradient(150deg,#3a5a2c,#6c8a48 40%,#5b4a34 65%,#7f9d5a)" role="img" aria-label="Climber in harness working among large twisting branches"></div>

  <a class="btn" style="left:545px;top:1519px;width:148px;height:36px;font-size:12px">View All Services</a>
</section>

<h2 class="section-title" style="top:3406px;color:var(--green)">Latest <span class="accent">News &amp;</span> Updates</h2>
<p class="section-lead" style="top:3484px">Lorem ipsum dolor sit amet, consectetur adipiscing elit, sed do eiusmod tempor incididunt ut labore et dolore magna aliqua.<br>Quis ipsum suspendisse ultrices gravida. Risus commodo viverra maecenas accumsan lacus vel facilisis.</p>

<article class="news-card" style="left:112px">
  <div class="news-photo" style="background:linear-gradient(120deg,#4a3a26,#7b6244 45%,#a08a5e 70%,#3e4a2e)" role="img" aria-label="Hands hugging a large tree trunk in a forest"><span class="news-date">13/06/2024</span></div>
  <h4 class="news-title">Lorem ipsum dolor sit amet, consectetur adipiscing elit, sed do eiusmod</h4>
  <p class="news-text">Lorem ipsum dolor sit amet, consectetur adipiscing elit, sed do eiusmod tempor incididunt ut labore et dolore magna aliqua. Quis ipsum suspendisse ultrices gravida.</p>
</article>
<article class="news-card" style="left:441px">
  <div class="news-photo" style="background:linear-gradient(170deg,#8aa0b8,#6c7d8a 40%,#5a4536 70%,#3b2e24)" role="img" aria-label="Bare trees marked with red bands against the sky"><span class="news-date">13/06/2024</span></div>
  <h4 class="news-title">Lorem ipsum dolor sit amet, consectetur adipiscing elit, sed do eiusmod</h4>
  <p class="news-text">Lorem ipsum dolor sit amet, consectetur adipiscing elit, sed do eiusmod tempor incididunt ut labore et dolore magna aliqua. Quis ipsum suspendisse ultrices gravida.</p>
</article>
<article class="news-card" style="left:773px">
  <div class="news-photo" style="background:linear-gradient(160deg,#c7c9c2,#7d8a5e 40%,#c99a2a 65%,#5a4a30)" role="img" aria-label="Yellow stump grinding machine working in a yard"><span class="news-date">13/06/2024</span></div>
  <h4 class="news-title">Lorem ipsum dolor sit amet, consectetur adipiscing elit, sed do eiusmod</h4>
  <p class="news-text">Lorem ipsum dolor sit amet, consectetur adipiscing elit, sed do eiusmod tempor incididunt ut labore et dolore magna aliqua. Quis ipsum suspendisse ultrices gravida.</p>
</article>

<section class="contact">
  <div class="photo contact-photo" role="img" aria-label="Arborist in a tree cutting branches with sawdust spraying"></div>
  <h2 class="contact-title">GET IN TOUCH</h2>
  <p class="contact-sub">We denounce with righteous indignation and dislike men</p>
  <div class="field" style="left:492px;top:163px;width:214px;height:40px">First Name</div>
  <div class="field" style="left:726px;top:163px;width:214px;height:40px">Last Name</div>
  <div class="field" style="left:492px;top:228px;width:214px;height:41px">Email Address</div>
  <div class="field" style="left:726px;top:228px;width:214px;height:41px">Contact Number</div>
  <div class="field" style="left:492px;top:293px;width:448px;height:108px">Message</div>
  <a class="send">SEND MESSAGE</a>
</section>

<footer class="site-footer">
  <div class="footer-brand"><span class="brand-mark"></span><span class="brand-name" style="font-size:40px;line-height:44px">VERDELL<br>TREE CARE</span></div>
  <nav class="footer-nav">
    <span>Home</span><span class="sep">|</span><span>About Us</span><span class="sep">|</span><span>Our Services</span><span class="sep">|</span><span>Blogs</span><span class="sep">|</span><span>Contact Us</span>
  </nav>
  <div class="socials"><span></span><span></span><span></span><span></span><span></span></div>
  <p class="copyright">(C) Copyright 2024 | All Rights Reserved</p>
</footer>

</body>
</html>
```